Grey Fennel Medical Website to make connecting and communicating easier

To create a unique, user-friendly, professional website for patients and professionals to access education/ information, forms, appointments, contact details, and data about us, and for us to have the capacity to link to various cloud-based platforms.
To use the logo design and colour scheme we have just sourced.

WEBSITE to be eye catching, Inspiring and alluring
- efficient and logical
- professional and trustworthy appearance
- health focus "living health matters"
- user friendly
- ability to link with cloud-based software and video conferencing tools/ telehealth
- colours- black/ white teal and ?silver

PAGES:
page 1 - Our clinic and staff, services offered, contact us- address/ map / contact details- social media connections
page 2- patients and visitors - New patient forms to complete, news and patient informtion (educatinal)
page 3 - health professionals -referral forms, research and education
page 3- online appointments
page 4 - Quick links - partners, other services
page 5- privacy policy, disclaimer

HI, Could we please extend the deadline another 5 days, so sorry just struggling with my workload to be able to keep up and I am wanting to liaise more with the designer that I will choose. I am so happy with SketchHarbor and all the designers - thank you! Thank you so much!!

Target Market(s)

Patients - mostly over 60's so the website must be minimal clicks and simple to navigate
Professionals - for education and access forms

Industry/Entity Type

Health Care

Coding

Coded - Design and coding required

Number of Pages Required

5+ page

Font styles to use
Sans Serif
Script

Colors
33b8a4
86cfc6

Requirements
Must have
• WEBSITE to be eye catching, Inspiring and alluring
- efficient and logical
- user friendly

WEBSITE - professional and user friendly
- ability to link with cloud based software and videoconferencing/ telehealth
Nice to have
• clean and crisp presentation
happy for an innovative look
room to add more services and ability to link pages and resources
Should not have
• Please ensure the website is not:
clunky
difficult to navigate
common and cheap looking

```html
<!DOCTYPE html>
<html lang="en">
<head>
<meta charset="utf-8">
<title>Grey Fennel Medical – Patients &amp; Visitors</title>
<link href="https://fonts.googleapis.com/css2?family=Roboto:wght@400;500&display=swap" rel="stylesheet">
<style>
:root{
  --teal:#33b8a4;
  --mint:#86cfc6;
  --mint-soft:#bdf1ec;
  --ink:#1b1b1b;
  --text:#555a5e;
  --white:#ffffff;
}
*{box-sizing:border-box;margin:0;padding:0}
html,body{width:1200px;height:2457px;overflow:hidden}
body{position:relative;font-family:'Roboto',Arial,sans-serif;color:var(--ink);background:var(--white)}
.abs{position:absolute}
.site-header{left:0;top:0;width:1200px;height:77px;background:var(--white)}
.brand{left:93px;top:22px;display:flex;align-items:center;gap:8px;font-size:15px;font-weight:500;color:var(--teal)}
.brand-dot{width:14px;height:14px;border-radius:50%;background:var(--teal)}
.main-nav a{position:absolute;top:34px;font-size:12.5px;color:var(--ink);text-decoration:none}
.main-nav a.is-active{color:var(--teal)}
.btn{display:inline-flex;align-items:center;justify-content:center;background:var(--teal);color:var(--white);font-size:12px;border-radius:2px;text-decoration:none}
.btn-contact{left:1006px;top:22px;width:105px;height:37px}
.hero{left:0;top:77px;width:1200px;height:375px;background:linear-gradient(120deg,#8d8f96,#a3a5ab 45%,#8a8c93)}
.hero-title{left:0;top:230px;width:1200px;text-align:center;color:var(--white);font-size:30px;font-weight:400}
.crumbs{left:0;top:281px;width:1200px;text-align:center;color:var(--white);font-size:12px}
.crumbs span{margin:0 9px}
.eyebrow{font-size:11.5px;color:var(--ink)}
.heading{font-size:29px;font-weight:400;line-height:35px;color:var(--ink)}
.copy{font-size:12.5px;line-height:20px;color:var(--text)}
.btn-appoint{left:93px;top:873px;width:160px;height:37px;font-weight:500}
.btn-appoint svg{margin-left:6px}
.footer{left:0;top:2052px;width:1200px;height:346px;background:var(--mint-soft)}
.footer h3{position:absolute;top:87px;font-size:20px;font-weight:400;color:#2a2a2a}
.footer ul{position:absolute;top:122px;list-style:none}
.footer li{font-size:12.5px;line-height:24px;color:#444}
.contact-row{display:flex;align-items:center;gap:10px;font-size:12px;line-height:22px;color:#444}
.socials{position:absolute;left:913px;top:212px;display:flex;gap:22px}
.socials span{width:16px;height:16px;border:2px solid #222;border-radius:50%}
.bottom-bar{left:0;top:2398px;width:1200px;height:59px;background:var(--teal);color:var(--white);font-size:12.5px;display:flex;justify-content:center;align-items:center;gap:42px}
</style>
</head>
<body>

<header class="site-header abs">
  <div class="brand abs"><span class="brand-dot"></span>Grey Fennel Medical</div>
  <nav class="main-nav">
    <a style="left:371px">Home</a>
    <a style="left:442px">Services</a>
    <a style="left:526px">Our Doctors</a>
    <a class="is-active" style="left:630px">Appoinments</a>
    <a style="left:737px">Patients &amp; visitors</a>
  </nav>
  <a class="btn btn-contact abs">Contacts Us</a>
</header>

<section class="hero abs" role="img" aria-label="Dentist treating a patient in a bright clinic room"></section>
<h1 class="hero-title abs">Patients &amp; Visitors</h1>
<div class="crumbs abs"><span>Home</span><span>Appoinments</span></div>

<section class="intro">
  <p class="eyebrow abs" style="left:93px;top:557px">Patients &amp; visitors</p>
  <h2 class="heading abs" style="left:93px;top:574px;width:440px">Informations That You Need For Your Visit</h2>
  <p class="copy abs" style="left:93px;top:660px;width:480px">Whether you’re visiting one of our locations or staying for an extended period, we are dedicated to ensuring that you have the most positive healthcare experience possible. This means providing not only the best care available, but also the information necessary to make accessing that care simple and convenient.</p>
  <p class="copy abs" style="left:93px;top:769px;width:470px">This section will provide you with all the information you need to visit any of our locations, register for an appointment, pay your bill online or visit a loved one. If you still have questions or concerns after reviewing this section, please contact the Brightwater Health location nearest you.</p>
  <a class="btn btn-appoint abs">Need An Appoinments
    <svg width="6" height="10" viewBox="0 0 6 10"><path d="M1 1l4 4-4 4" fill="none" stroke="#fff" stroke-width="1.5"/></svg></a>

  <svg class="abs" style="left:660px;top:460px" width="520" height="560" viewBox="660 460 520 560" aria-hidden="true">
    <circle cx="1011" cy="627" r="153" fill="var(--mint-soft)"/>
    <circle cx="754" cy="768" r="86" fill="var(--mint-soft)"/>
    <circle cx="935" cy="859" r="153" fill="var(--mint-soft)"/>
  </svg>
  <div class="abs" role="img" aria-label="Two smiling healthcare workers looking at a tablet" style="left:740px;top:537px;width:354px;height:417px;border-radius:30px;background:linear-gradient(135deg,#d6e9ef,#a9cfdc 55%,#e6eef0)"></div>
</section>

<section class="info">
  <p class="eyebrow abs" style="left:93px;top:1082px">Third parties requesting medical records</p>
  <h2 class="heading abs" style="left:93px;top:1098px;width:450px">What Third Party Representatives Need To Know</h2>
  <p class="copy abs" style="left:93px;top:1183px;width:430px">For a copy of medical records or other protected health information on behalf of a Grey Fennel patient, please submit a HIPAA compliant patient authorization or complete the Authorization to Disclose Protected Health or Billing Information form. Please submit this completed form to Grey Fennel Enterprise Release of Information by faxing it to 555-010-0207 or email your request to doctor@greyfennel.org. Since the request is not being made directly by the patient, but by a representative, the Patient Right of Access rules do not apply.</p>

  <p class="eyebrow abs" style="left:683px;top:1082px">Hospital stay</p>
  <h2 class="heading abs" style="left:683px;top:1098px;width:430px">Making Each And Every Experience Outstanding</h2>
  <p class="copy abs" style="left:683px;top:1183px;width:425px">We want your hospital stay to be as easy and comfortable as possible. We work every day to provide stress-free, compassionate environments in each of our facilities for you, your family and loved ones. Our teams of doctors, nurses and support staff are dedicated to making every step of your experience extraordinary.</p>

  <p class="eyebrow abs" style="left:93px;top:1409px">Third parties requesting medical records</p>
  <h2 class="heading abs" style="left:93px;top:1425px;width:450px">What Third Party Representatives Need To Know</h2>
  <p class="copy abs" style="left:93px;top:1510px;width:430px">For a copy of medical records or other protected health information on behalf of a Grey Fennel patient, please submit a HIPAA compliant patient authorization or complete the Authorization to Disclose Protected Health or Billing Information form. Please submit this completed form to Brightwater Health Enterprise Release of Information by faxing it to 555-014-2283 or email your request to doctor@greyfennel.org. Since the request is not being made directly by the patient, but by a representative, the Patient Right of Access rules do not apply.</p>

  <p class="eyebrow abs" style="left:683px;top:1419px">Medical records</p>
  <h2 class="heading abs" style="left:683px;top:1435px;width:430px">What's Included In My Medical Records?</h2>
  <p class="copy abs" style="left:683px;top:1520px;width:425px">Whether you’re visiting one of our locations or staying for an extended period, we are dedicated to ensuring that you have the most positive healthcare experience possible. This means providing not only the best care available, but also the information necessary to make accessing that care simple and convenient.</p>

  <p class="eyebrow abs" style="left:93px;top:1747px">Registration &amp; appointments</p>
  <h2 class="heading abs" style="left:93px;top:1763px;width:440px">At Grey Fennel, Making An Appointment And Preregistering Has Never Been Easier</h2>
  <p class="copy abs" style="left:93px;top:1883px;width:425px">Whether you’re visiting one of our locations or staying for an extended period, we are dedicated to ensuring that you have the most positive healthcare experience possible. This means providing not only the best care available, but also the information necessary to make accessing that care simple and convenient.</p>

  <p class="eyebrow abs" style="left:683px;top:1746px">Medical records</p>
  <h2 class="heading abs" style="left:683px;top:1762px;width:430px">What's Included In My Medical Records?</h2>
  <p class="copy abs" style="left:683px;top:1848px;width:425px">Whether you’re visiting one of our locations or staying for an extended period, we are dedicated to ensuring that you have the most positive healthcare experience possible. This means providing not only the best care available, but also the information necessary to make accessing that care simple and convenient.</p>
</section>

<footer class="footer abs">
  <h3 style="left:96px">Contact Us</h3>
  <div class="abs" style="left:96px;top:123px;width:210px">
    <p class="copy" style="color:#444;font-size:12.5px">Lorem ipsum dolor sit amet, consectetur adipiscing elit, sed do eiusmod tempor incididunt</p>
    <div class="contact-row" style="margin-top:2px"><svg width="12" height="14" viewBox="0 0 12 14"><path d="M6 0a5 5 0 0 0-5 5c0 4 5 9 5 9s5-5 5-9a5 5 0 0 0-5-5zm0 7a2 2 0 1 1 0-4 2 2 0 0 1 0 4z" fill="#222"/></svg>4200 Willow Lane CA, USA</div>
    <div class="contact-row"><svg width="12" height="12" viewBox="0 0 12 12"><path d="M2.5 0.5l2 2.5-1.2 1.5a7 7 0 0 0 4.2 4.2L9 7.5l2.5 2-1 2C5 11.5 0.5 7 0.5 1.5z" fill="#222"/></svg>+1-555-784-0144</div>
    <div class="contact-row"><svg width="12" height="10" viewBox="0 0 12 10"><rect x="0.6" y="0.6" width="10.8" height="8.8" fill="none" stroke="#222" stroke-width="1.2"/><path d="M0.6 0.6l5.4 4.5 5.4-4.5" fill="none" stroke="#222" stroke-width="1.2"/></svg>info@greyfennel.org</div>
  </div>

  <h3 style="left:399px">Quick Links</h3>
  <ul style="left:399px"><li>General information</li><li>Emergency service</li><li>Ambulance</li><li>Medical research</li><li>Blood bank</li><li>Intensive care service</li></ul>

  <h3 style="left:611px">Join Our Community</h3>
  <ul style="left:611px"><li>Blog postes</li><li>Join our forum</li><li>Meet our doctors</li><li>Medical research</li><li>Help center</li><li>Contract us</li></ul>

  <h3 style="left:913px">Open Time</h3>
  <ul style="left:913px"><li>Mon-Fri 8:00 AM - 10:00 PM</li><li>Sat-Sun 9:00 AM - 6:00 PM</li><li>Emergency 24/24 hours</li></ul>
  <div class="socials" aria-label="Social media links"><span></span><span></span><span></span><span></span></div>
</footer>

<div class="bottom-bar abs"><span>Copyright 2020 . All rights reserved</span><span>Grey Fennel</span></div>

</body>
</html>
```